Maple Roster Business Card for recruitment company

We are looking for a Business Card Design that incorporates our personal details and our busines name and logo. We are a specialized search consultancy that recruit Property and Construction professionals.
We would like a business card that stands out and is appealing to the Construction and Property industry as well.

Target Market(s)

people in the construction and property industry

Contact Information for Business Card

Business Name and logo

Font styles to use
Serif

Colors
0094D4
00A9DD
6FCCEA
C7EBF8
E9F6FB

Requirements
Must have
• Business name and logo as well as contact details
Should not have
• No photos of us please

```html
<!DOCTYPE html>
<html lang="en">
<head>
<meta charset="utf-8">
<title>Maple Roster Business Card</title>
<link href="https://fonts.googleapis.com/css2?family=Josefin+Sans:wght@300;700&family=Arimo:wght@400&display=swap" rel="stylesheet">
<style>
  :root {
    --backdrop: #b8b8b8;
    --navy: #033b4f;
    --paper: #ffffff;
    --ink-soft: #3a3a3a;
    --shadow: rgba(0, 0, 0, 0.65);
  }
  * { box-sizing: border-box; margin: 0; padding: 0; }
  html, body { width: 1075px; height: 1200px; overflow: hidden; }
  body { background: var(--backdrop); position: relative; font-family: "Arimo", Arial, sans-serif; }

  .card {
    position: absolute;
    left: 206px;
    width: 663px;
    height: 396px;
    box-shadow: 3px 3px 2px var(--shadow);
    overflow: hidden;
  }
  .card--front { top: 187px; background: var(--paper); }
  .card--back { top: 637px; background: var(--navy); }

  .brand-name {
    font-family: "Josefin Sans", sans-serif;
    font-weight: 300;
    letter-spacing: 2px;
    white-space: nowrap;
    line-height: 1;
  }
  .card--front .brand-name {
    position: absolute;
    right: 41px;
    top: 92px;
    font-size: 52px;
    color: var(--navy);
  }
  .card--back .brand-name {
    position: absolute;
    left: 0; right: 0;
    top: 172px;
    text-align: center;
    font-size: 60px;
    color: var(--paper);
  }

  .holder { position: absolute; left: 35px; top: 202px; }
  .holder__name {
    font-family: "Josefin Sans", sans-serif;
    font-weight: 700;
    font-size: 25px;
    letter-spacing: 0.5px;
    color: var(--navy);
    line-height: 1;
  }
  .holder__role {
    margin-top: 5px;
    font-size: 17px;
    letter-spacing: 0.3px;
    color: var(--ink-soft);
    line-height: 1;
  }

  .contact-band {
    position: absolute;
    left: 0; right: 0; bottom: 0;
    height: 130px;
    background: var(--navy);
    color: var(--paper);
    font-size: 18px;
  }
  .contact-list { position: absolute; left: 35px; top: 29px; list-style: none; }
  .contact-list li {
    display: flex;
    align-items: center;
    gap: 6px;
    height: 23.5px;
    line-height: 1;
  }
  .contact-list svg { width: 17px; height: 17px; flex: none; }

  .address {
    position: absolute;
    right: 41px;
    top: 56px;
    text-align: right;
    font-style: normal;
    line-height: 23.5px;
  }
</style>
</head>
<body>
  <section class="card card--front">
    <div class="brand-name">MAPLE ROSTER</div>

    <div class="holder">
      <div class="holder__name">DANIEL HARTLEY</div>
      <div class="holder__role">MANAGING DIRECTOR</div>
    </div>

    <div class="contact-band">
      <ul class="contact-list">
        <li>
          <svg viewBox="0 0 24 24" aria-hidden="true"><path fill="#fff" d="M6.6 10.8c1.4 2.8 3.8 5.1 6.6 6.6l2.2-2.2c.3-.3.7-.4 1-.2 1.1.4 2.3.6 3.6.6.6 0 1 .4 1 1V20c0 .6-.4 1-1 1C10.6 21 3 13.4 3 4c0-.6.4-1 1-1h3.5c.6 0 1 .4 1 1 0 1.3.2 2.5.6 3.6.1.3 0 .7-.2 1z"/><path fill="none" stroke="#fff" stroke-width="1.6" stroke-linecap="round" d="M14.5 3.5a6.5 6.5 0 0 1 6 6M14.5 7a3 3 0 0 1 2.6 2.6"/></svg>
          <span>044-987 654 321</span>
        </li>
        <li>
          <svg viewBox="0 0 24 24" aria-hidden="true"><rect x="2" y="5" width="20" height="14" fill="#fff"/><path fill="none" stroke="#033b4f" stroke-width="1.6" d="M2.5 5.5 12 13l9.5-7.5M2.5 18.5l7-6.5M21.5 18.5l-7-6.5"/></svg>
          <span>hello@mapleroster.com</span>
        </li>
        <li>
          <svg viewBox="0 0 24 24" aria-hidden="true"><g fill="none" stroke="#fff" stroke-width="1.6"><circle cx="12" cy="12" r="9.5"/><ellipse cx="12" cy="12" rx="4" ry="9.5"/><path d="M2.5 12h19M4 7h16M4 17h16"/></g></svg>
          <span>www.mapleroster.com</span>
        </li>
      </ul>
      <address class="address">
        421, Address line goes here<br>
        45452,Country Name
      </address>
    </div>
  </section>

  <section class="card card--back">
    <div class="brand-name">MAPLE ROSTER</div>
  </section>
</body>
</html>
```